Print materials for 3-star hotel

We are changing up our print materials (notepads, letterheads, key card jackets, small flyer for the room rates) We are a 3 star business hotel in the Philippines and have mainly used grey tones and clean, simple lines. See attached photos for logo and hotel interior photos.

Target Market(s)

Business

Contact Information for Business Card

Corvale Terrace Hotel
Lindwell Banca Avenue corner Tolenta St Cebu City 6000 Philippines
Tel: +63 32 481 7302
Mobile: +63 917 648 2095
www.corvaleterracehotel.example

Font styles to use
Serif
Sans Serif

Requirements
Must have
• Simple
• Readable font and font size
Nice to have
• Neutral colors, grey and taupes
Should not have
• No purples and bright blues

```html
<!DOCTYPE html>
<html lang="en">
<head>
<meta charset="utf-8">
<title>Corvale Terrace Hotel — Business Card</title>
<link rel="stylesheet" href="https://fonts.googleapis.com/css2?family=Crimson+Text:wght@400&family=Marcellus&display=swap">
<style>
  :root {
    --backdrop: #eceff0;
    --card: #c8c7c9;
    --card-edge: #b9b8ba;
    --ink: #f5f5f6;
    --shadow: rgba(60, 60, 70, 0.18);
  }
  * { margin: 0; padding: 0; box-sizing: border-box; }
  html, body {
    width: 1200px; height: 900px; overflow: hidden;
    background: var(--backdrop);
  }
  .canvas {
    width: 1200px; height: 900px;
    display: flex; flex-direction: column; align-items: center; justify-content: center;
    gap: 60px;
  }
  .card {
    width: 630px; height: 360px;
    background: var(--card);
    border-bottom: 3px solid var(--card-edge);
    box-shadow: 0 10px 24px var(--shadow);
    position: relative;
    color: var(--ink);
  }
  /* Front */
  .card-front {
    display: flex; flex-direction: column; align-items: center; justify-content: center;
  }
  .brand-mark {
    width: 44px; height: 44px;
    background: var(--ink);
    margin-bottom: 22px;
  }
  .brand-name {
    font-family: "Marcellus", serif;
    font-size: 30px;
    letter-spacing: 0.22em;
    text-transform: uppercase;
    text-align: center;
    line-height: 1.2;
  }
  .brand-name .brand-line-2 {
    display: block;
    font-size: 20px;
    letter-spacing: 0.36em;
  }
  /* Back */
  .card-back { padding: 46px 56px; }
  .person-name {
    font-family: "Marcellus", serif;
    font-size: 26px;
    letter-spacing: 0.08em;
    text-transform: uppercase;
  }
  .person-title {
    font-family: "Crimson Text", serif;
    font-size: 17px;
    margin-bottom: 18px;
  }
  .contact-block {
    font-family: "Crimson Text", serif;
    font-size: 16px;
    line-height: 1.3;
    margin-bottom: 14px;
  }
  .hotel-name {
    position: absolute; left: 56px; bottom: 40px;
    font-family: "Marcellus", serif;
    font-size: 16px;
    letter-spacing: 0.12em;
    text-transform: uppercase;
  }
</style>
</head>
<body>
<main class="canvas">
  <section class="card card-front" aria-label="Business card front">
    <div class="brand-mark"></div>
    <p class="brand-name">Corvale Terrace<span class="brand-line-2">Hotel</span></p>
  </section>

  <section class="card card-back" aria-label="Business card back">
    <h1 class="person-name">Adrian Velmonte</h1>
    <p class="person-title">CEO/Founder</p>
    <p class="contact-block">2146 Alder Crest Road<br>Cebu City, Cebu 6000</p>
    <p class="contact-block">p. +63 32 481 7302<br>c. +63 917 648 2095</p>
    <p class="contact-block">a.velmonte@corvaleterracehotel.example<br>www.corvaleterracehotel.example</p>
    <p class="hotel-name">Corvale Terrace Hotel</p>
  </section>
</main>
</body>
</html>
```